New business card for a regional office of a US M&A company

We need business card for a finance company, office based in Hong Kong , our Head office is in US, our business is to Merge and acquires companies , the new office will be a regional office for the Asia Pacific region. We want to use the head office logo as attached ( but don't have to be exactly the same, can be a variation to it) as a base and then add Asia Pacific alongside the logo.
We would prefer to have be bilingual Eng + Chinese, although we don't really have Chinese company name .

Industry/Entity Type

Business

Contact Information for Business Card

Clara Jo Tsang
 

VP,
APAC M&A Operations
Orin Vantage Asia Pacific Limited
 
Unit 1407, K18
18 Tai Lok Shan Road, 
Hong Kong 
 
M: +852 6038 1742
T : +852 2836 4100
F : +852 2836 4177
VOIP: 4158
 
cjtsang@orinvantage.com

Font styles to use
Serif
Sans Serif

Colors

Designer to choose colors to be used in the design.

Requirements
Must have
• APAC Office

```html
<!DOCTYPE html>
<html lang="en">
<head>
<meta charset="utf-8">
<title>Orin Vantage – APAC Business Card</title>
<link href="https://fonts.googleapis.com/css2?family=Open+Sans:wght@700&family=Roboto:wght@400;500&display=swap" rel="stylesheet">
<style>
  :root {
    --stage: #2b2b2b;
    --navy: #10293f;
    --cyan: #20a9d0;
    --paper: #eceff1;
    --ink: #1b2630;
    --white: #ffffff;
  }
  * { margin: 0; padding: 0; box-sizing: border-box; }
  html, body { width: 1200px; height: 960px; overflow: hidden; background: var(--stage); }
  .canvas { position: relative; width: 1200px; height: 960px; }

  .card { position: absolute; left: 320px; width: 600px; height: 344px; overflow: hidden; }
  .card-back { top: 108px; background: var(--navy); }
  .card-front { top: 492px; background: var(--navy); }

  .wordmark {
    font-family: "Open Sans", sans-serif; font-weight: 700;
    color: var(--cyan); white-space: nowrap; line-height: 1;
  }
  .card-back .wordmark { position: absolute; right: 32px; top: 248px; font-size: 44px; }
  .website {
    position: absolute; right: 30px; top: 296px;
    font-family: "Roboto", sans-serif; font-size: 15px; letter-spacing: 4.2px;
    color: var(--white);
  }

  .front-header { position: absolute; inset: 0 0 166px 0; }
  .front-header .wordmark {
    position: absolute; left: 0; right: 0; top: 112px; text-align: center; font-size: 38px;
  }
  .front-header .mark-square {
    position: absolute; left: 287px; top: 40px; width: 26px; height: 26px; background: var(--white);
  }

  .front-split { position: absolute; left: 0; top: 178px; width: 600px; height: 166px; }

  .office-details {
    position: absolute; left: 28px; top: 204px;
    font-family: "Roboto", sans-serif; font-size: 15px; line-height: 19px; color: var(--white);
  }
  .person { position: absolute; right: 30px; top: 204px; text-align: right; font-family: "Roboto", sans-serif; }
  .person-name { font-size: 19px; font-weight: 500; color: var(--cyan); line-height: 22px; }
  .person-title { font-size: 15px; color: var(--ink); line-height: 20px; }
  .phone-list { list-style: none; margin-top: 22px; }
  .phone-list li {
    display: flex; justify-content: flex-end; align-items: center; gap: 5px;
    font-size: 14.5px; color: var(--ink); line-height: 19px;
  }
  .phone-list svg { width: 13px; height: 13px; fill: var(--cyan); }
</style>
</head>
<body>
<main class="canvas">

  <section class="card card-back" aria-label="Card back">
    <div class="wordmark">ORIN VANTAGE</div>
    <div class="website">www.orinvantage.com</div>
  </section>

  <section class="card card-front" aria-label="Card front">
    <div class="front-header">
      <span class="mark-square"></span>
      <div class="wordmark">ORIN VANTAGE</div>
    </div>

    <svg class="front-split" viewBox="0 0 600 166" aria-hidden="true">
      <rect width="600" height="166" fill="var(--paper)"/>
      <polygon points="0,0 330,0 322,166 0,166" fill="var(--cyan)"/>
    </svg>

    <address class="office-details" style="font-style:normal">
      APAC M&amp;A Operations<br>
      Orin Vantage Asia Pacific Limited<br>
      Unit 1407, K18<br>
      18 Tai Lok Shan Road<br>
      Hong Kong<br>
      VOIP: 4158
    </address>

    <div class="person">
      <div class="person-name">CLARA JO TSANG</div>
      <div class="person-title">VP</div>
      <ul class="phone-list">
        <li>+852 2836 4100
          <svg viewBox="0 0 24 24" aria-label="Telephone"><path d="M6.6 10.8a15 15 0 0 0 6.6 6.6l2.2-2.2a1 1 0 0 1 1-.25 11.4 11.4 0 0 0 3.6.6 1 1 0 0 1 1 1V20a1 1 0 0 1-1 1A17 17 0 0 1 3 4a1 1 0 0 1 1-1h3.5a1 1 0 0 1 1 1c0 1.25.2 2.45.6 3.6a1 1 0 0 1-.25 1z"/></svg>
        </li>
        <li>+852 6038 1742
          <svg viewBox="0 0 24 24" aria-label="Mobile"><path d="M7 1h10a2 2 0 0 1 2 2v18a2 2 0 0 1-2 2H7a2 2 0 0 1-2-2V3a2 2 0 0 1 2-2zm0 3v14h10V4zm5 15.5a1.2 1.2 0 1 0 0 2.4 1.2 1.2 0 0 0 0-2.4z"/></svg>
        </li>
        <li>+852 2836 4177
          <svg viewBox="0 0 24 24" aria-label="Fax"><path d="M6 2h10l2 2v5H6zM3 10h18a2 2 0 0 1 2 2v7h-4v3H5v-3H1v-7a2 2 0 0 1 2-2zm4 7v3h10v-3z"/></svg>
        </li>
      </ul>
    </div>
  </section>

</main>
</body>
</html>
```